Business Cards - Brightpath Horizon

need to design unique business card for my mortgage business. I need to design credit card style business card for my business or any unique idea that you might have

Target Market(s)

Home Loan customers

Industry/Entity Type

Mortgage Brokerage

Contact Information for Business Card

please design credit card style or very unique style business card

Colors

Designer to choose colors to be used in the design.

Requirements
Must have
• Name
• position
• Phone number
• fax number
• email address
• website address
• social media address
• All above fields will be provided once design in finalised

```html
<!DOCTYPE html>
<html lang="en">
<head>
<meta charset="utf-8">
<title>Brightpath Horizon – Business Cards</title>
<link rel="stylesheet" href="https://fonts.googleapis.com/css2?family=Roboto:wght@400;500;700&family=Share+Tech+Mono&display=swap">
<style>
  :root{
    --bg:#e4e4e6;
    --card-dark:#1c1d1f;
    --card-light:#f6f6f6;
    --brand-blue:#0c3fd6;
    --brand-orange:#f7941d;
    --sky:#1ea0e6;
    --ink-grey:#5c5c5c;
    --white:#ffffff;
  }
  html,body{margin:0;padding:0;overflow:hidden;}
  body{width:1200px;height:886px;background:var(--bg);position:relative;font-family:"Roboto",Arial,sans-serif;}
  .card{position:absolute;width:620px;height:391px;border-radius:22px;overflow:hidden;box-shadow:0 10px 28px rgba(0,0,0,.25);}
  .card--front{left:80px;top:40px;background:var(--card-dark);}
  .card--back{left:500px;top:455px;background:var(--card-light);}

  .front__brand{position:absolute;left:0;right:0;top:140px;display:flex;align-items:center;justify-content:center;gap:14px;}
  .brand-mark{width:22px;height:22px;background:var(--sky);border-radius:50%;flex:none;}
  .front__name{font-weight:700;font-size:40px;color:var(--brand-orange);letter-spacing:.5px;}
  .front__web{position:absolute;left:0;right:0;bottom:66px;text-align:center;color:var(--white);font-size:15px;letter-spacing:9px;}

  .back__bands{position:absolute;inset:0;}
  .back__number{position:absolute;left:52px;top:118px;font-family:"Share Tech Mono",monospace;font-size:46px;color:var(--ink-grey);letter-spacing:4px;word-spacing:14px;white-space:nowrap;}
  .back__brand{position:absolute;right:34px;top:40px;display:flex;align-items:center;gap:10px;}
  .back__brand .brand-mark{width:16px;height:16px;}
  .back__name{font-weight:700;font-size:24px;color:var(--brand-blue);}
  .person{position:absolute;right:26px;top:194px;text-align:right;}
  .person__name{font-weight:700;font-size:22px;color:var(--brand-blue);}
  .person__title{font-weight:500;font-size:16px;color:var(--white);margin-top:2px;}
  .address{position:absolute;right:26px;top:272px;text-align:right;color:var(--white);font-size:15px;line-height:1.35;}
  .contact{position:absolute;left:46px;bottom:24px;color:var(--white);font-size:15px;line-height:1.45;}
  .contact b{font-family:Georgia,serif;font-weight:700;display:inline-block;width:22px;}
</style>
</head>
<body>
  <section class="card card--front">
    <div class="front__brand">
      <span class="brand-mark"></span>
      <span class="front__name">Brightpath Horizon</span>
    </div>
    <div class="front__web">www.brightpathhorizon.com</div>
  </section>

  <section class="card card--back">
    <svg class="back__bands" width="620" height="391" viewBox="0 0 620 391">
      <polygon points="410,182 620,182 620,262 386,262" fill="var(--brand-orange)"/>
      <polygon points="0,292 190,292 230,262 620,262 620,391 0,391" fill="var(--brand-blue)"/>
    </svg>
    <div class="back__brand">
      <span class="brand-mark"></span>
      <span class="back__name">Brightpath Horizon</span>
    </div>
    <div class="back__number">714 208 5963</div>
    <div class="person">
      <div class="person__name">DANIEL REYES</div>
      <div class="person__title">CEO/FOUNDER</div>
    </div>
    <div class="address">2140 Cedar Ridge Road<br>Boise, Idaho 83702</div>
    <div class="contact">
      <div><b>P:</b>415 555 0172</div>
      <div><b>E:</b>hello@brightpathhorizon.com</div>
      <div><b>W:</b>www.brightpathhorizon.com</div>
    </div>
  </section>
</body>
</html>
```